Redesign of business card for Cedar Ridge Mechanical

We are looking for a new design for our business cards for Cedar Ridge Mechanical. We are a plumbing & HVAC construction company, operating on the West Coast of Canada and USA. Logo attached.
Industry/Entity Type
Construction - Plumbing & HVAC
Contact Information for Business Card
Name, address, phone numbers, email, website address
Look and feel
Each slider illustrates characteristics of the customer's brand and the style your logo design should communicate.

```html
<!DOCTYPE html>
<html lang="en">
<head>
<meta charset="UTF-8">
<title>Cedar Ridge Mechanical – Business Card</title>
<link rel="stylesheet" href="https://fonts.googleapis.com/css2?family=Montserrat:wght@400;500;700&display=swap">
<style>
  :root {
    --stage: #d8d1c7;
    --card-clear: #e9e5df;
    --card-dark: #0b0b0b;
    --band-grey: #8c8780;
    --gold: #c8b48e;
    --gold-soft: #bfae8c;
    --ink: #1a1a1a;
    --muted: #bdb8b0;
  }
  * { margin: 0; padding: 0; box-sizing: border-box; }
  html, body { width: 1200px; height: 1047px; overflow: hidden; }
  body {
    background: var(--stage);
    font-family: "Montserrat", sans-serif;
    position: relative;
  }
  .card {
    position: absolute;
    left: 100px;
    top: 251px;
    width: 1000px;
    height: 545px;
    border-radius: 22px;
    overflow: hidden;
    background: var(--card-clear);
    box-shadow: 0 14px 40px rgba(0,0,0,0.18);
  }
  .card-shape { position: absolute; inset: 0; }
  .brand {
    position: absolute;
    right: 36px;
    top: 96px;
    display: flex;
    align-items: center;
    gap: 16px;
  }
  .brand-mark {
    width: 44px; height: 44px;
    background: var(--ink);
  }
  .brand-name {
    font-weight: 700;
    font-size: 26px;
    letter-spacing: 1.5px;
    color: var(--ink);
    text-transform: uppercase;
    line-height: 1.25;
  }
  .person {
    position: absolute;
    left: 42px;
    top: 280px;
  }
  .person-name {
    font-weight: 700;
    font-size: 34px;
    letter-spacing: 1px;
    color: var(--gold);
    line-height: 1.1;
  }
  .person-role {
    font-size: 24px;
    color: var(--muted);
    margin-top: 8px;
  }
  .divider {
    position: absolute;
    left: 42px; right: 34px;
    top: 383px;
    height: 2px;
    background: var(--gold-soft);
  }
  .contacts {
    position: absolute;
    left: 40px;
    top: 403px;
    list-style: none;
  }
  .contacts li {
    display: flex;
    align-items: center;
    gap: 8px;
    font-size: 23px;
    color: var(--gold);
    height: 39px;
  }
  .contacts svg { width: 20px; height: 20px; flex: none; }
  .address {
    position: absolute;
    right: 34px;
    top: 446px;
    text-align: right;
    font-size: 23px;
    line-height: 39px;
    color: var(--gold);
  }
</style>
</head>
<body>
  <section class="card" aria-label="Cedar Ridge Mechanical business card">
    <svg class="card-shape" viewBox="0 0 1000 545" preserveAspectRatio="none" aria-hidden="true">
      <defs>
        <linearGradient id="band" x1="0" x2="1" y1="0" y2="0">
          <stop offset="0" stop-color="#3c3a37"/>
          <stop offset="0.5" stop-color="#9a958d"/>
          <stop offset="1" stop-color="#7d7871"/>
        </linearGradient>
      </defs>
      <path d="M0 248 C 220 228, 420 250, 600 292 C 760 328, 880 300, 1000 236 L1000 545 L0 545 Z" fill="url(#band)"/>
      <path d="M0 258 C 220 240, 420 264, 600 306 C 760 342, 880 318, 1000 262 L1000 545 L0 545 Z" fill="var(--card-dark)"/>
    </svg>

    <div class="brand">
      <span class="brand-mark"></span>
      <span class="brand-name">Cedar Ridge Mechanical</span>
    </div>

    <div class="person">
      <p class="person-name">DANIEL HART</p>
      <p class="person-role">Managing Director</p>
    </div>

    <div class="divider"></div>

    <ul class="contacts">
      <li>
        <svg viewBox="0 0 24 24" fill="var(--gold)"><path d="M6.6 10.8a15 15 0 0 0 6.6 6.6l2.2-2.2c.3-.3.7-.4 1-.2 1.1.4 2.3.6 3.6.6.6 0 1 .4 1 1V20c0 .6-.4 1-1 1A17 17 0 0 1 3 4c0-.6.4-1 1-1h3.5c.6 0 1 .4 1 1 0 1.3.2 2.5.6 3.6.1.3 0 .7-.2 1z"/></svg>
        123 456 789
      </li>
      <li>
        <svg viewBox="0 0 24 24" fill="none" stroke="var(--gold)" stroke-width="2"><rect x="3" y="6" width="18" height="13" rx="1"/><path d="M3 7l9 7 9-7"/></svg>
        info@cedarridgemech.com
      </li>
      <li>
        <svg viewBox="0 0 24 24" fill="none" stroke="var(--gold)" stroke-width="2"><circle cx="12" cy="12" r="9"/><path d="M3 12h18M12 3c3 3 3 15 0 18M12 3c-3 3-3 15 0 18"/></svg>
        www.cedarridgemech.com
      </li>
    </ul>

    <p class="address">Your address, City<br>State, Zip 1234</p>
  </section>
</body>
</html>
```